Modern Business Card

Modern professional business card with more than just logo and demographic info. Something memorable.

We are a trendy/modern chiropractic group with an emphasis on neurology, hence the minimalist-type brain logo. We want to convey that modern and technical aspect with professionalism and the elite nature of our practice environment.

```html
<!DOCTYPE html>
<html lang="en">
<head>
<meta charset="utf-8">
<title>Keystone Chiropractic – Business Card</title>
<link rel="stylesheet" href="https://fonts.googleapis.com/css2?family=Cinzel:wght@500&family=Roboto:wght@400;500&display=swap">
<style>
  :root {
    --page: #e9e9e9;
    --card: #252525;
    --edge: #4a7fcc;
    --accent: #4a80d0;
    --ink: #f2f2f2;
    --muted: #bdbdbd;
    --rule: #6a6a6a;
  }
  * { box-sizing: border-box; margin: 0; padding: 0; }
  html, body { width: 1200px; height: 801px; overflow: hidden; }
  body {
    background: var(--page);
    font-family: "Roboto", Arial, sans-serif;
    display: flex;
    align-items: center;
    justify-content: center;
    gap: 60px;
  }
  .card {
    position: relative;
    width: 525px;
    height: 300px;
    background: var(--card);
    border-bottom: 4px solid var(--edge);
    box-shadow: 0 10px 24px rgba(0,0,0,.18);
    overflow: hidden;
  }
  .wordmark {
    font-family: "Cinzel", Georgia, serif;
    font-weight: 500;
    color: var(--ink);
    line-height: .95;
  }
  .wordmark .line-1 { display: block; letter-spacing: .02em; }
  .wordmark .line-2 { display: block; letter-spacing: .04em; }

  /* Front */
  .card-front .brand {
    position: absolute;
    left: 48px; top: 62px;
    display: flex; align-items: center; gap: 14px;
  }
  .brand-square { width: 34px; height: 34px; background: var(--accent); }
  .card-front .wordmark .line-1 { font-size: 36px; }
  .card-front .wordmark .line-2 { font-size: 20px; }
  .person { position: absolute; left: 48px; top: 150px; }
  .person-name { color: var(--accent); font-size: 22px; font-weight: 500; }
  .person-role { color: var(--muted); font-size: 15px; margin-top: 4px; padding-left: 90px; }
  .divider {
    position: absolute; left: 300px; top: 120px;
    width: 1px; height: 64px; background: var(--rule);
  }
  .contacts {
    position: absolute; left: 318px; top: 112px;
    list-style: none; color: var(--muted); font-size: 14px;
  }
  .contacts li { display: flex; align-items: center; gap: 9px; height: 26px; }
  .contacts svg { width: 12px; height: 12px; fill: none; stroke: var(--accent); stroke-width: 1.6; }
  .contacts .hl { color: var(--accent); }
  .address {
    position: absolute; left: 48px; bottom: 36px;
    color: var(--muted); font-size: 14px;
  }

  /* Back */
  .mark-field {
    position: absolute; left: 0; top: 40px;
    width: 280px; height: 260px;
    background: linear-gradient(160deg, #2e2e2e 0%, #5a5a5a 55%, #8a8a8a 100%);
    border-radius: 0 40px 0 0;
  }
  .card-back .wordmark {
    position: absolute; right: 26px; top: 150px; text-align: left;
  }
  .card-back .wordmark .line-1 { font-size: 52px; }
  .card-back .wordmark .line-2 { font-size: 29px; }
</style>
</head>
<body>
  <section class="card card-front" aria-label="Card front">
    <div class="brand">
      <span class="brand-square"></span>
      <div class="wordmark">
        <span class="line-1">KEYSTONE</span>
        <span class="line-2">CHIROPRACTIC</span>
      </div>
    </div>
    <div class="person">
      <p class="person-name">Daniel Porter</p>
      <p class="person-role">Manager</p>
    </div>
    <span class="divider"></span>
    <ul class="contacts">
      <li>
        <svg viewBox="0 0 12 12"><path d="M3 1 L5 3 L4 5 Q5 7 7 8 L9 7 L11 9 L9 11 Q3 10 1 3 Z"/></svg>
        555-318-2740
      </li>
      <li>
        <svg viewBox="0 0 12 12"><rect x="1" y="2.5" width="10" height="7"/><path d="M1 2.5 L6 6.5 L11 2.5"/></svg>
        hello@keystonechiro.com
      </li>
      <li>
        <svg viewBox="0 0 12 12"><circle cx="6" cy="6" r="5"/><path d="M1 6 H11 M6 1 Q3 6 6 11 Q9 6 6 1"/></svg>
        <span>www.<span class="hl">keystonechiro</span>.com</span>
      </li>
    </ul>
    <p class="address">48 Elm Row, Fairview, OH 43210</p>
  </section>

  <section class="card card-back" aria-label="Card back">
    <div class="mark-field" role="img" aria-label="Large grey gradient brand symbol decoration"></div>
    <div class="wordmark">
      <span class="line-1">KEYSTONE</span>
      <span class="line-2">CHIROPRACTIC</span>
    </div>
  </section>
</body>
</html>
```